BrimFalcon Business Cards

We have a defined brand. Please visit our website to get a feel for the product and the color pallets. www.brimfalcon-example.com

We need an updated, world class business card design. (See the attached existing card design). Please utilize BOTH sides of the card as shown and be creative with the layout. I do want the horse head icon to be positioned as it is with the existing card.

The remainder of the layout can be customized and I also want it vertically oriented.

Attached are the logo files and please use the colors as follows:
Green - #A5CE39
Tan - #CDBD99
Black

Feel free to play with the colors.

```html
<!DOCTYPE html>
<html lang="en">
<head>
<meta charset="utf-8">
<title>BrimFalcon Business Cards</title>
<link rel="stylesheet" href="https://fonts.googleapis.com/css2?family=Muli:wght@400;600;700&display=swap">
<style>
  :root {
    --backdrop: #b9bdbd;
    --card-white: #f1f2f0;
    --card-black: #2a2b2b;
    --brand-green: #7fb02e;
    --brand-lime: #a5ce39;
    --ink: #5b5d5c;
    --ink-soft: #8a8c8b;
    --emboss: #dcdedc;
    --wordmark: #4a4c4c;
  }
  * { box-sizing: border-box; margin: 0; padding: 0; }
  html, body {
    width: 1200px; height: 880px; overflow: hidden;
    background: var(--backdrop);
    font-family: "Muli", "Mulish", sans-serif;
  }
  .canvas {
    position: relative; width: 1200px; height: 880px;
    display: flex; justify-content: center; align-items: center; gap: 80px;
  }
  .card {
    position: relative; width: 400px; height: 700px;
    border-bottom: 8px solid var(--brand-lime);
    box-shadow: 0 18px 40px rgba(0,0,0,0.18);
  }
  .card--front { background: var(--card-white); }
  .card--back {
    background: var(--card-black);
    display: flex; align-items: center; justify-content: center;
  }

  .front-emblem {
    position: absolute; left: 40px; top: 60px; width: 320px; height: 300px;
    display: flex; flex-direction: column; align-items: center; justify-content: center; gap: 22px;
  }
  .front-emblem__disc {
    width: 170px; height: 170px; border-radius: 50%;
    background: radial-gradient(circle at 35% 30%, #fafbfa, var(--emboss));
    box-shadow: inset -3px -3px 6px rgba(0,0,0,0.08), inset 3px 3px 6px rgba(255,255,255,0.9);
  }
  .front-emblem__name {
    font-size: 30px; font-weight: 600; letter-spacing: 1px; color: var(--emboss);
  }

  .contact {
    position: absolute; left: 48px; bottom: 64px; right: 40px;
    color: var(--ink);
  }
  .contact__name {
    font-size: 30px; font-weight: 700; letter-spacing: 1px;
    color: var(--brand-green); text-transform: uppercase;
  }
  .contact__title { font-size: 20px; margin-top: 6px; }
  .contact__place { font-size: 20px; margin-top: 28px; line-height: 1.35; }
  .contact__list { list-style: none; margin-top: 28px; font-size: 18px; line-height: 1.65; }
  .contact__list li { display: flex; align-items: center; gap: 10px; }
  .contact__icon { width: 14px; height: 14px; flex: none; }

  .wordmark { display: flex; align-items: center; gap: 14px; }
  .wordmark__dot { width: 34px; height: 34px; border-radius: 50%; background: #333535; }
  .wordmark__text { font-size: 36px; font-weight: 700; color: var(--wordmark); letter-spacing: 0.5px; }
</style>
</head>
<body>
<main class="canvas">
  <section class="card card--front" aria-label="Card front">
    <div class="front-emblem">
      <div class="front-emblem__disc"></div>
      <div class="front-emblem__name">BrimFalcon</div>
    </div>
    <div class="contact">
      <h1 class="contact__name">Dana Merrow</h1>
      <p class="contact__title">President &amp; CEO</p>
      <p class="contact__place">Harrow Bay, Westmere<br>Calderra</p>
      <ul class="contact__list">
        <li>
          <svg class="contact__icon" viewBox="0 0 14 14"><circle cx="7" cy="7" r="7" fill="var(--brand-lime)"/><path d="M4.5 3.5l1.5 1.6-.8 1a5 5 0 0 0 2.7 2.7l1-.8 1.6 1.5-.9 1.2c-3 0-6.2-3.2-6.2-6.2z" fill="#fff"/></svg>
          555.014.7391
        </li>
        <li>
          <svg class="contact__icon" viewBox="0 0 14 14"><rect width="14" height="14" rx="2" fill="var(--brand-lime)"/><path d="M3 4.5h8v5H3z M3 4.5l4 3 4-3" fill="none" stroke="#fff" stroke-width="1"/></svg>
          dana@brimfalcon-example.com
        </li>
        <li>
          <svg class="contact__icon" viewBox="0 0 14 14"><circle cx="7" cy="7" r="7" fill="var(--brand-lime)"/><circle cx="7" cy="7" r="4" fill="none" stroke="#fff" stroke-width="1"/><path d="M3 7h8M7 3c-1.6 2.4-1.6 5.6 0 8M7 3c1.6 2.4 1.6 5.6 0 8" fill="none" stroke="#fff" stroke-width="0.8"/></svg>
          brimfalconlabs-example.com
        </li>
      </ul>
    </div>
  </section>

  <section class="card card--back" aria-label="Card back">
    <div class="wordmark">
      <span class="wordmark__dot"></span>
      <span class="wordmark__text">BrimFalcon Labs</span>
    </div>
  </section>
</main>
</body>
</html>
```